Construction business card

I need a new business card, they can connect with my logo, brand.
What we do is residential house , design and build
I like: Navy blue / black
I attached our logo, brand,
and, some idea for business card.

```html
<!DOCTYPE html>
<html lang="en">
<head>
<meta charset="utf-8">
<title>Harlow Building Group – Business Card</title>
<link rel="stylesheet" href="https://fonts.googleapis.com/css2?family=Arimo:wght@400;700&display=swap">
<style>
  :root{
    --stage:#262626;
    --card:#3a87c7;
    --card-deep:#3079b8;
    --ink:#ffffff;
    --ink-soft:rgba(255,255,255,.85);
  }
  *{box-sizing:border-box;margin:0;padding:0}
  html,body{width:1200px;height:801px;overflow:hidden;background:var(--stage)}
  .stage{position:relative;width:1200px;height:801px;font-family:"Arimo",Arial,sans-serif;color:var(--ink)}
  .card{
    position:absolute;top:250px;width:520px;height:300px;border-radius:20px;
    background:linear-gradient(135deg,var(--card) 0%,var(--card-deep) 100%);
    overflow:hidden;
  }
  .card--front{left:50px}
  .card--back{left:630px}
  .card__diagonal{position:absolute;inset:0;width:100%;height:100%}
  .brand{position:absolute;font-weight:700;text-transform:uppercase;line-height:1;color:var(--ink)}
  .card--front .brand{left:34px;top:40px}
  .brand__name{display:block;font-size:38px;letter-spacing:1px}
  .brand__sub{display:block;font-size:13px;letter-spacing:2.6px;margin-top:6px}
  .address{position:absolute;right:30px;bottom:40px;text-align:right;font-size:12.5px;line-height:1.45}
  .person{position:absolute;left:34px;top:146px}
  .person__name{font-size:20px;font-weight:700;text-transform:uppercase;letter-spacing:.5px}
  .person__role{font-size:13px;color:var(--ink-soft);margin-top:3px}
  .person__rule{width:190px;height:1px;background:var(--ink);margin:10px 0 10px}
  .contacts{list-style:none;font-size:12.5px;line-height:1}
  .contacts li{display:flex;align-items:center;gap:7px;margin-bottom:7px}
  .contacts svg{width:11px;height:11px;flex:none}
  .card--back .brand{left:0;right:0;top:108px;text-align:center}
  .card--back .brand__name{font-size:58px;letter-spacing:2px}
  .card--back .brand__sub{font-size:18px;letter-spacing:4px;margin-top:10px}
</style>
</head>
<body>
<main class="stage">
  <section class="card card--front" aria-label="Business card front">
    <svg class="card__diagonal" viewBox="0 0 520 300" aria-hidden="true">
      <line x1="230" y1="300" x2="446" y2="30" stroke="#ffffff" stroke-width="0.8" opacity=".85"/>
    </svg>
    <div class="brand">
      <span class="brand__name">Harlow</span>
      <span class="brand__sub">Building Group</span>
    </div>
    <p class="address">42 Ashgrove Rd<br>Eastfield, VIC 3999</p>
    <div class="person">
      <h1 class="person__name">Daniel Reeve</h1>
      <p class="person__role">CEO/Founder</p>
      <div class="person__rule"></div>
      <ul class="contacts">
        <li><svg viewBox="0 0 12 12"><circle cx="6" cy="6" r="6" fill="#fff"/><path d="M4 3.2l1 1.3-.6.8a4 4 0 0 0 2.3 2.3l.8-.6 1.3 1-.6 1A5 5 0 0 1 3 4z" fill="#3a87c7"/></svg>0400 555 017</li>
        <li><svg viewBox="0 0 12 12"><circle cx="6" cy="6" r="6" fill="#fff"/><rect x="3" y="4" width="6" height="4.2" fill="none" stroke="#3a87c7" stroke-width=".9"/><path d="M3 4l3 2.3L9 4" fill="none" stroke="#3a87c7" stroke-width=".9"/></svg>info@harlowbuilding.com.au</li>
        <li><svg viewBox="0 0 12 12"><circle cx="6" cy="6" r="6" fill="#fff"/><circle cx="6" cy="6" r="3.3" fill="none" stroke="#3a87c7" stroke-width=".8"/><path d="M2.7 6h6.6M6 2.7c-1.6 2-1.6 4.6 0 6.6M6 2.7c1.6 2 1.6 4.6 0 6.6" fill="none" stroke="#3a87c7" stroke-width=".7"/></svg>harlowbuilding.com.au</li>
      </ul>
    </div>
  </section>
  <section class="card card--back" aria-label="Business card back">
    <div class="brand">
      <span class="brand__name">Harlow</span>
      <span class="brand__sub">Building Group</span>
    </div>
  </section>
</main>
</body>
</html>
```